Brivolt Technologies business card design

We need a business card designed with our new logo. it would be great if the card could communicate it is a technology based company.

Target Market(s)

system integrators

Industry/Entity Type

technology, IOT

Contact Information for Business Card

Name, designation, Address, telephone number, email address

Requirements
Must have
• logo and company name
Nice to have
• something to do with technology

```html
<!DOCTYPE html>
<html lang="en">
<head>
<meta charset="utf-8">
<title>Brivolt Technologies – Business Card</title>
<link rel="stylesheet" href="https://fonts.googleapis.com/css2?family=Open+Sans:wght@400;600;700&display=swap">
<style>
  :root {
    --stage: #3a3a3a;
    --card: #151515;
    --card-edge: #f39200;
    --accent: #f39200;
    --ink: #ffffff;
    --ink-soft: #e6e6e6;
    --mark-light: #5a5a5a;
    --mark-dark: #1b1b1b;
  }
  * { box-sizing: border-box; margin: 0; padding: 0; }
  html, body {
    width: 1200px; height: 801px; overflow: hidden;
    background: var(--stage);
    font-family: "Open Sans", Arial, sans-serif;
  }
  .stage {
    width: 1200px; height: 801px;
    display: flex; align-items: center; justify-content: center; gap: 50px;
  }
  .card {
    position: relative;
    width: 525px; height: 300px;
    background: var(--card);
    border-bottom: 3px solid var(--card-edge);
    border-left: 1px solid var(--card-edge);
    box-shadow: 0 18px 40px rgba(0,0,0,.45);
    overflow: hidden;
  }
  /* Front */
  .brand {
    position: absolute; top: 40px; right: 40px;
    display: flex; align-items: center; gap: 10px;
  }
  .brand-square { width: 18px; height: 18px; background: var(--accent); }
  .brand-name {
    font-weight: 700; font-size: 22px; letter-spacing: 1px;
    color: var(--ink); text-transform: uppercase;
  }
  .divider {
    position: absolute; left: 40px; right: 40px; top: 150px;
    height: 1px; background: var(--accent);
  }
  .address {
    position: absolute; right: 40px; top: 104px;
    text-align: right; color: var(--ink-soft);
    font-size: 13px; line-height: 1.35;
  }
  .person { position: absolute; left: 40px; top: 166px; }
  .person-name {
    color: var(--accent); font-weight: 700; font-size: 19px;
    text-transform: uppercase; letter-spacing: .3px;
  }
  .person-role { color: var(--ink-soft); font-size: 13px; margin-top: 2px; }
  .contacts {
    position: absolute; left: 40px; bottom: 28px;
    list-style: none; color: var(--ink-soft); font-size: 13px; line-height: 1.55;
  }
  .contacts li { display: flex; align-items: center; gap: 8px; }
  .contacts svg { width: 11px; height: 11px; fill: var(--accent); flex: none; }
  /* Back */
  .back-decor {
    position: absolute; left: 0; top: 0; width: 300px; height: 300px;
    background: radial-gradient(ellipse at 55% 45%, var(--mark-light) 0%, var(--mark-dark) 65%, transparent 100%);
    opacity: .55;
  }
  .back-brand {
    position: absolute; right: 36px; bottom: 54px;
    display: flex; align-items: center; gap: 12px;
  }
  .back-brand .brand-square { width: 22px; height: 22px; }
  .back-brand .brand-name { font-size: 30px; }
</style>
</head>
<body>
<main class="stage">
  <section class="card card-front" aria-label="Card front">
    <div class="brand">
      <span class="brand-square"></span>
      <span class="brand-name">Brivolt Technologies</span>
    </div>
    <p class="address">1870 Harbor Crest Way<br>Seaview CA 90412</p>
    <div class="divider"></div>
    <div class="person">
      <p class="person-name">Daniel Rourke</p>
      <p class="person-role">President</p>
    </div>
    <ul class="contacts">
      <li><svg viewBox="0 0 12 12"><path d="M2.5 1h2l1 3-1.5 1a6 6 0 0 0 3 3l1-1.5 3 1v2a1 1 0 0 1-1 1A10 10 0 0 1 1.5 2a1 1 0 0 1 1-1z"/></svg>555-018-3427</li>
      <li><svg viewBox="0 0 12 12"><path d="M1 2.5h10v7H1z M1 2.5l5 4 5-4" stroke="#151515" stroke-width="1"/></svg>hello@brivolttech.com</li>
      <li><svg viewBox="0 0 12 12"><circle cx="6" cy="6" r="5"/></svg>www.brivolttech.com</li>
    </ul>
  </section>

  <section class="card card-back" aria-label="Card back">
    <div class="back-decor" role="img" aria-label="Large faint brand symbol decoration"></div>
    <div class="back-brand">
      <span class="brand-square"></span>
      <span class="brand-name">Brivolt Technologies</span>
    </div>
  </section>
</main>
</body>
</html>
```